2020-23 Strategic Plan - Graphic Design Work

We would would like to have our strategic plan designed. It should be two pages.

- I am looking for suggestions on ways to lay this out. I don’t like this boxy layout. It was great for the committee as we went through multiple versions, but I’d prefer the final not follow this boxy format

- I’ve included a few images we own (feel free to use any or none of them). Also attached our logo.

- Have a look at our new website to see our new branding look and feel (launching next week) https://ourvelmora.hostpage-qx.net/

- I've included a copy of our logo.

Target Market(s)

Membership

Other font styles liked:
• Lato

Requirements
Must have
• Excellent layout. Easy to ready. Consistent with branding.

```html
<!DOCTYPE html>
<html lang="en">
<head>
<meta charset="utf-8">
<title>VIPA 2020-2023 Strategic Plan</title>
<link rel="stylesheet" href="https://fonts.googleapis.com/css2?family=Montserrat:wght@500;700;800;900&family=Raleway:ital,wght@0,300;0,400;1,400;1,500&display=swap">
<style>
:root{
  --backdrop:#d1d2d4;
  --paper:#fbfbfb;
  --band:#e5e7e9;
  --green:#4c9a3f;
  --green-soft:#5ea352;
  --forest:#0b4526;
  --red:#e01e29;
  --ink:#2b2b2b;
  --grey-head:#5a5a5a;
}
*{margin:0;padding:0;box-sizing:border-box}
html,body{width:1200px;height:896px;overflow:hidden;background:var(--backdrop)}
body{position:relative;font-family:"Raleway",sans-serif;color:var(--ink)}
.page{position:absolute;top:114px;width:481px;height:680px;background:var(--paper);overflow:hidden}
.page--cover{left:105px}
.page--pillars{left:614px}
.abs{position:absolute}

/* cover */
.brand{left:36px;top:32px;display:flex;align-items:center;gap:8px}
.brand__mark{width:22px;height:22px;background:var(--green)}
.brand__text{font-family:"Montserrat",sans-serif;font-weight:800;color:var(--forest);line-height:1}
.brand__name{font-size:38px;letter-spacing:1px}
.brand__full{font-size:7.6px;letter-spacing:.2px;margin-top:5px}
.site-url{left:313px;top:47px;font-family:"Raleway",sans-serif;font-weight:400;font-size:14.5px;color:var(--forest);letter-spacing:.3px}
.hero-photo{left:0;top:114px;width:481px;height:243px;background:linear-gradient(160deg,#2a3b6e 0%,#6a5b93 35%,#b07b9e 55%,#5b4f86 75%,#1f2c55 100%)}
.plan-year{left:35px;top:207px;font-family:"Montserrat",sans-serif;font-weight:500;font-size:39px;color:#fff;letter-spacing:1px}
.plan-title{left:34px;top:250px;font-family:"Montserrat",sans-serif;font-weight:900;font-size:43px;color:#fff;letter-spacing:-.5px;white-space:nowrap}
.accent-block{left:35px;top:301px;width:58px;height:122px;background:var(--red)}
.intro-box{left:103px;top:301px;width:344px;height:122px;background:var(--green-soft);padding:14px 16px 0 14px;font-style:italic;font-weight:500;font-size:12.3px;line-height:15.4px;color:#fff}
.statement{top:438px;width:126px}
.statement h2{font-family:"Montserrat",sans-serif;font-weight:800;font-size:27px;line-height:32px;margin-bottom:3px}
.statement p{font-weight:300;font-size:8.3px;line-height:9.7px;text-align:justify;color:var(--ink)}
.statement--vision{left:35px}.statement--vision h2{color:var(--green)}
.statement--mission{left:179px}.statement--mission h2{color:var(--forest)}
.statement--values{left:322px}.statement--values h2{color:var(--grey-head)}
.history{left:35px;top:580px;width:415px;font-style:italic;font-weight:500;font-size:8.2px;line-height:9.8px;text-align:justify;color:#111}
.footer-band{left:0;top:636px}

/* pillars */
.band-shade{left:0;width:481px;background:var(--band)}
.rule{height:6px;background:var(--green)}
.pillar-title{left:27px;font-family:"Montserrat",sans-serif;font-weight:900;font-size:33px;letter-spacing:1px;line-height:1;white-space:nowrap}
.pillar-title--light{color:var(--green)}
.pillar-title--dark{color:var(--forest)}
.col{position:absolute}
.col--objective{left:28px;width:115px}
.col--goals{left:162px;width:145px}
.col--actions{left:330px;width:130px}
.col h3{font-family:"Montserrat",sans-serif;font-weight:700;font-size:9px;line-height:10.6px;letter-spacing:1px;color:var(--forest);margin-bottom:5px}
.col p{font-weight:400;font-size:6.3px;line-height:7.8px;color:var(--ink);margin-bottom:7.8px}
</style>
</head>
<body>

<section class="page page--cover">
  <div class="abs brand">
    <div class="brand__mark"></div>
    <div class="brand__text">
      <div class="brand__name">VIPA</div>
      <div class="brand__full">VELMORA INSTITUTE OF PROPERTY ASSESSORS</div>
    </div>
  </div>
  <div class="abs site-url">www.velmoravipa.ca</div>

  <div class="abs hero-photo" role="img" aria-label="Upward view of glass city skyscrapers against a streaked purple and pink sky"></div>
  <div class="abs plan-year">2020-2023</div>
  <div class="abs plan-title">STRAGETIC PLAN</div>

  <div class="abs accent-block"></div>
  <div class="abs intro-box">With over 1,250 members, the Velmora Institute of Property Assessors is Canada's largest association of property assessment and taxation professionals. Our dverse membership is comprised of individuals from the private and public sectors practicing in the fields of assessment, consultancy, appraisal, taxation and law.</div>

  <div class="abs statement statement--vision">
    <h2>Vision</h2>
    <p>To be the industry leader in education, ethical standards, and professional accreditation in the field of property assessment in Canada.</p>
  </div>
  <div class="abs statement statement--mission">
    <h2>Mission</h2>
    <p>To provide specialized education through a comprehensive approach to training which embraces all available technologies. To promote professional development and to ensure our members are recognized as experts in the field of property assessment and related functions.</p>
  </div>
  <div class="abs statement statement--values">
    <h2>Values</h2>
    <p>The Velmora Institute of Property Assessors and its members value professionalism, inclusivity, diversity, integrity, ethics, accountability, and expertise. The VIPA is committed to serving all members and stakeholders with competence and respect, rejecting all forms of prejudice and discrimination.</p>
  </div>

  <p class="abs history">Incorporated in May 1957, the VIPA is dedicated to advancing the interests, education and professional competence of its members. Our members are highly qualified and widely recognized as the leading professionals in the property assessment industry.</p>

  <svg class="abs footer-band" width="481" height="44" viewBox="0 0 481 44" aria-hidden="true">
    <polygon points="0,0 176,0 198,17 481,17 481,44 0,44" fill="var(--forest)"/>
    <polygon points="185,7 481,7 481,12 192,12" fill="var(--green)"/>
  </svg>
</section>

<section class="page page--pillars">
  <!-- Educate -->
  <div class="abs band-shade" style="top:54px;height:142px"></div>
  <div class="abs rule" style="left:224px;top:47px;width:257px"></div>
  <div class="abs pillar-title pillar-title--light" style="top:41px">EDUCATE</div>
  <div class="col col--objective" style="top:79px">
    <h3>STRATEGIC<br>OBJECTIVE</h3>
    <p>Be the most trusted, relevant, and accessible provider of education and credentials in the field of property assessment in Canada</p>
  </div>
  <div class="col col--goals" style="top:79px">
    <h3>STRATEGIC<br>GOALS</h3>
    <p>Ensure a catalogue of relevant, high-quality courses, which meet the evolving needs of assessment professionals</p>
    <p>Provide an equal VIPA member experience and service, regardless of geography</p>
  </div>
  <div class="col col--actions" style="top:79px">
    <h3>SAMPLE SUPPORTING<br>ACTIONS</h3>
    <p>Utilize technology to offer interactive and accessible online events</p>
    <p>Develop provincial legislation-specific content for VIPA courses</p>
    <p>Lead opportunities for collaboration across districts to increase access to quality PD opportunities</p>
  </div>

  <!-- Grow -->
  <div class="abs pillar-title pillar-title--dark" style="top:200px">GROW</div>
  <div class="col col--objective" style="top:238px">
    <h3>STRATEGIC<br>OBJECTIVE</h3>
    <p>Increase the VIPA's membership by serving all career levels and forging strong strategic partnerships.</p>
  </div>
  <div class="col col--goals" style="top:238px">
    <h3>STRATEGIC<br>GOALS</h3>
    <p>Enhance opportunities for senior assessment professionals through the FVIPA designation.</p>
    <p>Connect with young professionals by enhancing member communications, improving member onboarding, and expanding scholarship opportunities.</p>
  </div>
  <div class="col col--actions" style="top:238px">
    <h3>SAMPLE SUPPORTING<br>ACTIONS</h3>
    <p>Develop framework for a specialist designation track</p>
    <p>Work collaboratively with strategic partners from across the country to develop criteria for, and launch, the FVIPA designation</p>
    <p>Redesign the new member onboarding experience</p>
  </div>

  <!-- Lead -->
  <div class="abs band-shade" style="top:362px;height:143px"></div>
  <div class="abs rule" style="left:224px;top:356px;width:257px"></div>
  <div class="abs pillar-title pillar-title--light" style="top:349px">LEAD</div>
  <div class="col col--objective" style="top:387px">
    <h3>STRATEGIC<br>OBJECTIVE</h3>
    <p>Strengthen the reputation of the organization and its members by acting as a leader within the field of property assessment in Canada</p>
  </div>
  <div class="col col--goals" style="top:387px">
    <h3>STRATEGIC<br>GOALS</h3>
    <p>Embrace the role of leader and advocate within the property assessment profession.</p>
    <p>Strengthen current, and develop new, strategic partnerships with peer associations across Canada.</p>
  </div>
  <div class="col col--actions" style="top:387px">
    <h3>SAMPLE SUPPORTING<br>ACTIONS</h3>
    <p>Adopt an advocacy voice for the assessment profession to ensure interests are being represented</p>
    <p>Work with strategic partners to produce industry white papers with national relevance</p>
    <p>Engage with various levels of government across Canada</p>
  </div>

  <!-- Govern -->
  <div class="abs pillar-title pillar-title--dark" style="top:509px">GOVERN</div>
  <div class="col col--objective" style="top:547px">
    <h3>STRATEGIC<br>OBJECTIVE</h3>
    <p>Fortify the future of the VIPA through operational excellence and a diverse group of talented volunteers</p>
  </div>
  <div class="col col--goals" style="top:547px">
    <h3>STRATEGIC<br>GOALS</h3>
    <p>Review and align association management practices with strategic objectives and statements of Vision, Mission and Values.</p>
    <p>Secure the VIPA's financial stability by reviewing current pricing model and practicing sound risk management.</p>
  </div>
  <div class="col col--actions" style="top:547px">
    <h3>SAMPLE SUPPORTING<br>ACTIONS</h3>
    <p>Align the VIPA budget and staffing needs to achieve clear strategic objectives</p>
    <p>Utilize automation to modernize systems and administrative processes</p>
    <p>Review and assess the relevance of current committees to determine if sufficient to meet the requirements of the strategic plan, and create new committees if deemed relevant</p>
  </div>
</section>

</body>
</html>
```